Business Card for a New Zealand IT Startup

I need a business card for VELTA Holdings. We are a young startup based in New Zealand working in internet marketing and web development. The design should have some element connected to New Zealand, such as wave, koru or silver fern, just don't use a kiwi bird.

```html
<!DOCTYPE html>
<html lang="en">
<head>
<meta charset="utf-8">
<title>VELTA Holdings — Business Card</title>
<link href="https://fonts.googleapis.com/css2?family=Open+Sans:wght@400;600;700&display=swap" rel="stylesheet">
<style>
  :root{
    --stage:#3a3a3c;
    --card:#28292c;
    --blue:#1a78c9;
    --orange:#f0621e;
    --white:#f4f4f4;
    --muted:#d8d8d8;
  }
  *{box-sizing:border-box;margin:0;padding:0}
  html,body{width:799px;height:1200px;overflow:hidden}
  body{
    background:var(--stage);
    font-family:"Open Sans",Arial,sans-serif;
    position:relative;
  }
  .card{
    position:absolute;
    left:90px;
    width:620px;
    height:354px;
    background:var(--card);
    border-radius:22px;
    overflow:hidden;
    box-shadow:0 14px 30px rgba(0,0,0,.35);
  }
  .card--front{top:120px}
  .card--back{top:700px}

  .wordmark{
    display:flex;
    align-items:center;
    gap:12px;
    color:var(--blue);
    font-weight:700;
    letter-spacing:1px;
    white-space:nowrap;
  }
  .wordmark__dot{
    border-radius:50%;
    background:var(--blue);
    flex:none;
  }

  /* front */
  .card--front .wordmark{
    position:absolute;
    left:0;right:0;top:110px;
    justify-content:center;
    font-size:46px;
    line-height:60px;
  }
  .card--front .wordmark__dot{width:22px;height:22px}
  .front-web{
    position:absolute;
    left:0;right:0;top:232px;
    display:flex;
    align-items:center;
    justify-content:center;
    gap:18px;
    color:var(--white);
    font-size:17px;
    line-height:24px;
  }
  .front-web__rule{width:70px;height:3px;background:var(--blue)}
  .hl-blue{color:var(--blue)}
  .hl-orange{color:var(--orange)}

  /* back */
  .card--back .wordmark{
    position:absolute;
    left:34px;top:82px;
    font-size:28px;
    line-height:36px;
    gap:10px;
  }
  .card--back .wordmark__dot{width:18px;height:18px}
  .contact{
    position:absolute;
    left:360px;top:74px;
    width:240px;
    color:var(--white);
  }
  .contact__name{
    color:var(--blue);
    font-size:21px;
    font-weight:700;
    line-height:1.15;
  }
  .contact__role{
    font-size:12px;
    color:var(--muted);
    margin-bottom:16px;
  }
  .contact__address{
    font-size:14px;
    line-height:1.4;
    margin-bottom:4px;
  }
  .contact__line{
    display:flex;
    align-items:center;
    gap:10px;
    font-size:14px;
    line-height:1.65;
  }
  .contact__icon{width:14px;height:14px;flex:none}
  .back-band{
    position:absolute;
    left:0;bottom:0;
    width:620px;height:80px;
  }
  .back-web{
    position:absolute;
    right:40px;bottom:15px;
    color:var(--white);
    font-size:17px;
    line-height:24px;
  }
</style>
</head>
<body>

  <section class="card card--front" aria-label="Card front">
    <div class="wordmark"><span class="wordmark__dot"></span>VELTA Holdings</div>
    <div class="front-web">
      <span class="front-web__rule"></span>
      <span>www.<span class="hl-blue">velta</span><span class="hl-orange">holdings</span>.com</span>
      <span class="front-web__rule"></span>
    </div>
  </section>

  <section class="card card--back" aria-label="Card back">
    <div class="wordmark"><span class="wordmark__dot"></span>VELTA Holdings</div>

    <div class="contact">
      <p class="contact__name">Mara Tane Ellis</p>
      <p class="contact__role">Managing Director</p>
      <p class="contact__address">18 Harbour Lane, Northcote,<br>Auckland, NZ 0627</p>
      <p class="contact__line">
        <svg class="contact__icon" viewBox="0 0 16 16" aria-hidden="true"><path fill="#f0621e" d="M3.6 1.5l2.3 2.6-1.2 1.7c.9 2 2.5 3.6 4.5 4.5l1.7-1.2 2.6 2.3-1.2 2.3C7 14.8 1.2 9 1.3 2.7z"/></svg>
        021-555-0148
      </p>
      <p class="contact__line">
        <svg class="contact__icon" viewBox="0 0 16 16" aria-hidden="true"><rect x="1" y="3" width="14" height="10" fill="#f0621e"/><path d="M1.5 3.5L8 9l6.5-5.5" fill="none" stroke="#28292c" stroke-width="1.4"/></svg>
        hello@veltaholdings.com
      </p>
    </div>

    <svg class="back-band" viewBox="0 0 620 80" preserveAspectRatio="none" aria-hidden="true">
      <rect x="0" y="66" width="330" height="14" fill="#f0621e"/>
      <path class="back-band__wave" d="M286 80 C300 70 304 44 326 34 C348 24 372 30 400 36 C440 44 470 22 510 24 C550 26 580 34 620 28 L620 80 Z" fill="#1a78c9"/>
    </svg>
    <p class="back-web">www.veltaholdings.com</p>
  </section>

</body>
</html>
```